Roofing Company Realtor Marketing Flyer

We would like a design for marketing material aimed at realtors. We are seeking to build relationships with local realtors to ensure that both sellers and buyers are happy and confident with their roofing systems through roof inspections, No-Leak certification, roof repairs, and replacements if necessary.

There are three points that must be included:
1. Home inspectors are generalists. We are roof experts that specialize in diagnosing and fixing roofing problems.
2. We offer "No Leak" certification to offer peace of mind to homeowners.
3. We offer referral bonuses for realtors.

Target Market(s)

Realtors

Industry/Entity Type

Roofing

Font styles to use
Sans Serif

Colors

Designer to choose colors to be used in the design.

Requirements
Must have
• Must be double-sided.
• Must be similar to current marketing materials design. See website http://gablecrestpro.example and attached images for details.
• We would also like a "fanned out" version of our Sample Inspection Report showing glimpses of some of the images on the later pages (See attached documents).

```html
<!DOCTYPE html>
<html lang="en">
<head>
<meta charset="utf-8">
<title>Gable Crest – Realtor Flyer</title>
<link rel="stylesheet" href="https://fonts.googleapis.com/css2?family=Open+Sans:wght@400;600;700;800&family=Oswald:wght@500;600&display=swap">
<style>
  :root{
    --orange:#f28a1c;
    --orange-deep:#e5761a;
    --ink:#2c2c2c;
    --grey-text:#6b6b6b;
    --band:#d9d9d9;
    --bar:#2b2b2b;
    --white:#ffffff;
  }
  *{box-sizing:border-box;margin:0;padding:0}
  html,body{width:851px;height:1200px;overflow:hidden;background:var(--white)}
  .flyer{position:relative;width:851px;height:1200px;background:var(--white);font-family:"Open Sans",sans-serif;color:var(--ink);overflow:hidden}

  .brand{position:absolute;left:44px;top:38px;display:flex;align-items:center;gap:12px}
  .brand-mark{width:22px;height:22px;background:var(--orange)}
  .brand-name{font-size:46px;font-weight:700;color:var(--orange);letter-spacing:-0.5px}
  .site{position:absolute;right:48px;top:58px;font-size:17px;font-weight:600;color:var(--grey-text)}

  .hero{position:absolute;left:0;top:112px;width:851px;height:480px}

  .services-tab{position:absolute;left:450px;top:560px;width:401px;height:58px;background:var(--orange);border-radius:30px 0 0 30px;color:var(--white);font-size:36px;font-weight:600;display:flex;align-items:center;padding-left:64px}

  .pitch{position:absolute;left:44px;top:690px;width:400px}
  .pitch-title{font-family:"Oswald",sans-serif;font-size:44px;font-weight:600;line-height:1.05;text-transform:uppercase;color:var(--ink)}
  .pitch-title .accent{color:var(--orange)}
  .pitch-body{margin-top:10px;font-size:19px;font-weight:600;line-height:1.25;text-transform:uppercase;color:var(--ink)}

  .services{position:absolute;left:496px;top:646px;list-style:none;border-left:2px solid #cfcfcf;padding-left:26px}
  .services li{display:flex;align-items:center;gap:18px;height:48px;font-size:25px;color:var(--ink)}
  .services svg{width:28px;height:28px;flex:none}

  .offer-tab{position:absolute;left:305px;top:858px;width:240px;height:50px;background:var(--orange);border-radius:8px 8px 0 0;color:var(--white);font-size:30px;font-weight:600;display:flex;align-items:center;justify-content:center}
  .offer{position:absolute;left:0;top:906px;width:851px;height:196px;background:var(--band);text-align:center;padding-top:22px}
  .offer-line{font-size:39px;font-weight:600;line-height:1.2;color:var(--ink);text-transform:uppercase}
  .offer-line.strong{font-weight:700;margin-top:10px;color:#242424}

  .cta{position:absolute;left:0;top:1112px;width:851px;height:88px;background:var(--bar);display:flex;align-items:center;color:var(--white)}
  .cta-label{font-size:28px;font-weight:700;padding-left:36px;text-transform:uppercase;letter-spacing:.3px}
  .cta-arrow{width:46px;height:88px;margin-left:14px}
  .cta-phone{display:flex;align-items:center;gap:12px;font-size:30px;font-weight:600;margin-left:20px}
  .cta-phone svg{width:28px;height:28px}
</style>
</head>
<body>
<div class="flyer">

  <header>
    <div class="brand"><span class="brand-mark"></span><span class="brand-name">Gable Crest</span></div>
    <div class="site">www.gablecrestpro.example</div>
  </header>

  <svg class="hero" viewBox="0 0 851 480" xmlns="http://www.w3.org/2000/svg">
    <defs>
      <linearGradient id="houseTone" x1="0" y1="0" x2="0" y2="1">
        <stop offset="0" stop-color="#c9d6e2"/>
        <stop offset=".45" stop-color="#6d6f73"/>
        <stop offset="1" stop-color="#5f7a3e"/>
      </linearGradient>
      <linearGradient id="roofTone" x1="0" y1="0" x2="1" y2="1">
        <stop offset="0" stop-color="#8b6d58"/>
        <stop offset="1" stop-color="#4e4540"/>
      </linearGradient>
      <linearGradient id="workTone" x1="0" y1="0" x2="1" y2="1">
        <stop offset="0" stop-color="#a08571"/>
        <stop offset="1" stop-color="#5d4c42"/>
      </linearGradient>
      <linearGradient id="chimneyTone" x1="0" y1="0" x2="0" y2="1">
        <stop offset="0" stop-color="#d3d6d8"/>
        <stop offset="1" stop-color="#585656"/>
      </linearGradient>
    </defs>

    <rect x="0" y="0" width="851" height="470" fill="url(#houseTone)" role="img" aria-label="Photo of a large stone house with a dark shingle roof and front lawn"/>
    <polygon points="0,470 851,250 851,480 0,480" fill="var(--white)"/>
    <polygon points="0,400 851,170 851,250 0,470" fill="var(--orange)"/>
    <polygon points="0,470 520,330 851,250 851,270 520,352 0,480" fill="var(--orange-deep)" opacity=".6"/>

    <circle cx="640" cy="210" r="165" fill="var(--orange)"/>
    <circle cx="640" cy="210" r="150" fill="url(#workTone)" role="img" aria-label="Photo of a roofer in a hard hat working on shingles"/>

    <circle cx="245" cy="318" r="86" fill="var(--white)"/>
    <circle cx="245" cy="318" r="78" fill="url(#roofTone)" role="img" aria-label="Close-up photo of a shingle roof edge"/>

    <circle cx="420" cy="405" r="80" fill="var(--white)"/>
    <circle cx="420" cy="405" r="72" fill="url(#chimneyTone)" role="img" aria-label="Photo of a chimney on a shingle roof"/>
  </svg>

  <div class="services-tab">What we do?</div>

  <section class="pitch">
    <h1 class="pitch-title">Home inspectors<br><span class="accent">are generalists</span></h1>
    <p class="pitch-body">We are roof experts that specialize in diagnosing and fixing roofing problems</p>
  </section>

  <ul class="services">
    <li><svg viewBox="0 0 28 28"><path d="M4 14 L14 5 L24 14 M7 12 V23 H21 V12" fill="none" stroke="var(--orange)" stroke-width="3"/></svg>Roof Repairs</li>
    <li><svg viewBox="0 0 28 28"><path d="M22 9 A9 9 0 1 0 23 17 M22 3 V9 H16" fill="none" stroke="var(--orange)" stroke-width="3"/></svg>Replacements</li>
    <li><svg viewBox="0 0 28 28"><circle cx="12" cy="12" r="7" fill="none" stroke="var(--orange)" stroke-width="3"/><path d="M17 17 L25 25" stroke="var(--orange)" stroke-width="3"/></svg>Roof Inspections</li>
    <li><svg viewBox="0 0 28 28"><circle cx="14" cy="14" r="11" fill="var(--orange)"/><path d="M8 14 L12 18 L20 10" fill="none" stroke="#fff" stroke-width="3"/></svg>No-leak Certification</li>
  </ul>

  <div class="offer-tab">We Offer</div>
  <section class="offer">
    <p class="offer-line">"No Leak" certification to<br>offer peace of mind to homeowners</p>
    <p class="offer-line strong">Referral bonuses for realtors</p>
  </section>

  <footer class="cta">
    <span class="cta-label">Request a free estimate</span>
    <svg class="cta-arrow" viewBox="0 0 46 88"><polygon points="0,0 20,0 46,44 20,88 0,88 26,44" fill="var(--orange)"/></svg>
    <span class="cta-phone">
      <svg viewBox="0 0 28 28"><path d="M7 3 L11 3 L13 9 L10 11 C11 14 14 17 17 18 L19 15 L25 17 L25 21 C25 23 23 25 21 25 C12 24 4 16 3 7 C3 5 5 3 7 3 Z" fill="#fff"/></svg>
      (555) 014-ROOF
    </span>
  </footer>

</div>
</body>
</html>
```